Business Cards for new orthopaedic surgery practice

My husband and I are starting our own orthopaedic surgery practice. We are looking for a business card that is uniform, but one will have my name/title and the other will have his. You can just create one design with my name on it for now. But when I choose your design as the winning design I will ask that you add another copy with his name/title.

We are looking for classy, simple, elite all in one. We like dark blues/a little gold/yellow. Something that goes with our logo. We want our logo incorporated. Here is all the info you need:
Business name: RV Bone & Vitality Center
Location: 38517 North Willowmere Ave
Maple Harbor, FL 33492
Phone: 954-218-4063
Fax: 954-582-7341
Email: info@myrvbonecare.example

Names: Lydia Vance, M.D.
Board Certified Hand and Upper Extremity Surgeon

Ebo Dansu, M.D.
Board Certified Hip & Knee Replacement/General Orthopaedic Surgeon

Can decide what you want to put on the back. Maybe a slogan:
Built on Trust. Centered on You

I am just going to upload our logo. The only thing is if we select you as the winning design, the location, and phone numbers may change. We will need your help to update that once fully solidified.

Industry/Entity Type

Medical

Contact Information for Business Card

Colors
0054AA
0677BA
7BADD7
CADEEF
E8F1F8
0094D4
00A9DD
6FCCEA
C7EBF8
E9F6FB

Requirements
Must have
• class, appeal,
Should not have
• We want to air on the side of masculine if we are looking at masculine vs. feminine feel. But we still want it classy, sophisticated, and something we will love

```html
<!DOCTYPE html>
<html lang="en">
<head>
<meta charset="utf-8">
<title>RV Bone &amp; Vitality Center – Business Card</title>
<link rel="stylesheet" href="https://fonts.googleapis.com/css2?family=Playfair+Display:wght@400&family=Poppins:wght@400;500;600;700&display=swap">
<style>
  :root {
    --backdrop: #c4c4c4;
    --paper: #ffffff;
    --navy: #141c44;
    --ink: #17204a;
    --gold: #c9a45c;
    --white: #ffffff;
  }
  * { margin: 0; padding: 0; box-sizing: border-box; }
  html, body { width: 800px; height: 1200px; overflow: hidden; }
  body {
    background: var(--backdrop);
    position: relative;
    font-family: "Poppins", sans-serif;
  }
  .card {
    position: absolute;
    left: 80px;
    width: 640px;
    height: 366px;
    box-shadow: 6px 8px 14px rgba(0,0,0,0.28);
    overflow: hidden;
  }
  .card--front { top: 194px; background: var(--paper); color: var(--ink); }
  .card--back  { top: 640px; background: var(--navy); color: var(--white); }

  .divider {
    position: absolute;
    left: 296px;
    top: 102px;
    width: 1px;
    height: 160px;
    background: var(--gold);
  }

  .doctor-name {
    position: absolute;
    left: 50px;
    top: 96px;
    font-family: "Playfair Display", serif;
    font-weight: 400;
    font-size: 39px;
    line-height: 43px;
    letter-spacing: 0.5px;
    text-transform: uppercase;
  }
  .doctor-title {
    position: absolute;
    left: 50px;
    top: 206px;
    padding-left: 10px;
    border-left: 2px solid var(--gold);
    font-size: 14px;
    font-weight: 500;
    line-height: 19px;
    letter-spacing: 1.3px;
    text-transform: uppercase;
  }

  .contact-list {
    position: absolute;
    left: 355px;
    top: 106px;
    list-style: none;
    font-size: 14.5px;
    letter-spacing: 0.8px;
    line-height: 20px;
  }
  .contact-item { display: flex; align-items: flex-start; margin-bottom: 18px; }
  .contact-item:first-child { margin-bottom: 16px; }
  .contact-icon { width: 16px; height: 16px; margin-right: 9px; margin-top: 2px; flex-shrink: 0; }

  .practice-mark {
    position: absolute;
    left: 52px;
    top: 112px;
    width: 200px;
    height: 140px;
    display: flex;
    flex-direction: column;
    align-items: center;
    justify-content: center;
    gap: 14px;
  }
  .practice-mark__dot {
    width: 22px; height: 22px;
    border-radius: 50%;
    background: var(--gold);
  }
  .practice-mark__name {
    font-weight: 500;
    font-size: 17px;
    line-height: 24px;
    letter-spacing: 2.5px;
    text-transform: uppercase;
    text-align: center;
    color: var(--white);
  }

  .slogan {
    position: absolute;
    left: 371px;
    top: 128px;
    font-size: 26px;
    line-height: 27.5px;
    letter-spacing: 3px;
    text-transform: uppercase;
  }
  .slogan__line { display: block; font-weight: 400; }
  .slogan__line--strong { font-weight: 700; }
  .slogan__line--gold { color: var(--gold); }
</style>
</head>
<body>
  <section class="card card--front" aria-label="Business card front">
    <h1 class="doctor-name">Lydia<br>Vance, M.D.</h1>
    <p class="doctor-title">Board Certified<br>Hand &amp; Upper<br>Extremity Surgeon</p>
    <div class="divider"></div>
    <ul class="contact-list">
      <li class="contact-item">
        <svg class="contact-icon" viewBox="0 0 16 16"><path d="M8 1a5 5 0 0 0-5 5c0 3.6 5 9 5 9s5-5.4 5-9a5 5 0 0 0-5-5zm0 7a2 2 0 1 1 0-4 2 2 0 0 1 0 4z" fill="#c9a45c"/></svg>
        <span>38517 North Willowmere Ave<br>Maple Harbor, FL 33492</span>
      </li>
      <li class="contact-item">
        <svg class="contact-icon" viewBox="0 0 16 16"><path d="M4 1.5l2 3-1.3 1.6a8 8 0 0 0 5.2 5.2L11.5 10l3 2-1 2.3C7.5 14.7 1.3 8.5 1.7 2.5z" fill="#c9a45c"/></svg>
        <span>954-218-4063</span>
      </li>
      <li class="contact-item">
        <svg class="contact-icon" viewBox="0 0 16 16"><rect x="4" y="1.5" width="8" height="4" fill="#c9a45c"/><rect x="1.5" y="6" width="13" height="6" rx="1" fill="#c9a45c"/><rect x="4" y="10" width="8" height="4.5" fill="#fff" stroke="#c9a45c" stroke-width="1.4"/></svg>
        <span>954-582-7341</span>
      </li>
      <li class="contact-item">
        <svg class="contact-icon" viewBox="0 0 16 16"><rect x="1" y="3.5" width="14" height="9.5" fill="#c9a45c"/><path d="M1 3.5l7 5.5 7-5.5" fill="none" stroke="#fff" stroke-width="1.2"/></svg>
        <span>info@myrvbonecare.example</span>
      </li>
    </ul>
  </section>

  <section class="card card--back" aria-label="Business card back">
    <div class="practice-mark">
      <span class="practice-mark__dot"></span>
      <span class="practice-mark__name">RV Bone &amp;<br>Vitality Center</span>
    </div>
    <div class="divider"></div>
    <p class="slogan">
      <span class="slogan__line">Built on</span>
      <span class="slogan__line slogan__line--strong">Trust</span>
      <span class="slogan__line slogan__line--gold">Centered on</span>
      <span class="slogan__line slogan__line--gold slogan__line--strong">You</span>
    </p>
  </section>
</body>
</html>
```